Business card design for holistic health care clinic

We need a double-sided business card design for our holistic health care clinic that integrates our logo design and also its color scheme. My business is called Valmira. It is an integrative medicine clinic. You have already done the logo for me. Please ensure an elegant and upscale design that is not cluttered, but still has all the necessary information (please see below for details).

Target Market(s)

Wellness, fitness, rehabilitation for educated, well-traveled open-minded clients who are focused on natural, organic, balanced and preventive healthcare and lifestyle.

Industry/Entity Type

Medical

Contact Information for Business Card

Modern, clean.

Number of Pages Required

1 page

Font styles to use
Serif
Sans Serif

Colors

Designer to choose colors to be used in the design.

Requirements
Must have
• Logo on one side, all other information on the other side.
• Other information should include:
• Tobias Wrenfeld - DOE, CPT, LMT
• 4100 East Marrow Drive
• Austin, TX 78119
• 512 555 0148
• 818 555 0192
• info@ValmiraHealth.example
• t.wrenfeld@ValmiraHealth.example
Nice to have
• Darker background on front - but not totally black - shaded/dark gray.

```html
<!DOCTYPE html>
<html lang="en">
<head>
<meta charset="utf-8">
<title>Valmira – Business Card</title>
<link href="https://fonts.googleapis.com/css2?family=Nunito:wght@700;800&family=Roboto:ital,wght@0,400;1,300&family=Roboto+Condensed:wght@700&display=swap" rel="stylesheet">
<style>
  :root {
    --brand-blue: #0a88d0;
    --ink: #3a3a3a;
    --paper: #f7f7f7;
    --slate: #232323;
    --backdrop: #e6e3de;
  }
  * { box-sizing: border-box; margin: 0; padding: 0; }
  html, body { width: 1200px; height: 800px; overflow: hidden; }
  body {
    background: var(--backdrop);
    display: flex;
    align-items: center;
    justify-content: center;
    gap: 48px;
    font-family: "Roboto", Arial, sans-serif;
  }
  .card {
    position: relative;
    width: 520px;
    height: 297px;
    border-radius: 3px;
    box-shadow: 0 10px 28px rgba(0,0,0,0.18);
    overflow: hidden;
  }

  /* Info side */
  .card--info { background: var(--paper); }
  .brand {
    font-family: "Nunito", Arial, sans-serif;
    color: var(--brand-blue);
  }
  .brand__name {
    display: flex;
    align-items: center;
    gap: 8px;
    font-weight: 800;
    text-transform: uppercase;
    line-height: 1;
  }
  .brand__dot {
    border-radius: 50%;
    background: var(--brand-blue);
    flex: none;
  }
  .brand__tagline { font-weight: 700; }

  .card--info .brand { position: absolute; left: 34px; top: 72px; }
  .card--info .brand__name { font-size: 38px; letter-spacing: 1px; }
  .card--info .brand__dot { width: 11px; height: 11px; }
  .card--info .brand__tagline { font-size: 12.5px; margin-top: 4px; }

  .holder {
    position: absolute;
    left: 34px;
    bottom: 52px;
    font-family: "Roboto Condensed", Arial, sans-serif;
    font-weight: 700;
    color: var(--brand-blue);
    font-size: 20px;
    text-transform: uppercase;
  }
  .holder__credentials { font-size: 12px; }

  .contact {
    position: absolute;
    right: 26px;
    top: 70px;
    width: 214px;
    color: var(--ink);
    font-size: 11.5px;
    line-height: 1.45;
    white-space: nowrap;
  }
  .contact__address { margin-bottom: 10px; }
  .contact__row { display: flex; align-items: center; gap: 7px; }
  .contact__icon { width: 11px; height: 11px; flex: none; fill: var(--brand-blue); }
  .contact__group + .contact__group { margin-top: 6px; }

  /* Brand side */
  .card--brand { background: var(--slate); }
  .card--brand .brand {
    position: absolute;
    left: 0; right: 0; top: 82px;
    text-align: center;
  }
  .card--brand .brand__name { justify-content: center; font-size: 56px; letter-spacing: 2px; }
  .card--brand .brand__dot { width: 14px; height: 14px; }
  .card--brand .brand__tagline { font-size: 15px; margin-top: 6px; }
  .motto-band {
    position: absolute;
    left: 0; right: 0; bottom: 22px;
    height: 34px;
    background: var(--brand-blue);
    color: #e9f4fb;
    font-style: italic;
    font-weight: 300;
    font-size: 15px;
    display: flex;
    align-items: flex-end;
    justify-content: center;
    padding-bottom: 3px;
  }
</style>
</head>
<body>

  <section class="card card--info" aria-label="Business card, contact side">
    <div class="brand">
      <div class="brand__name"><span class="brand__dot"></span>Valmira</div>
      <div class="brand__tagline">Integrative Holistic Medicine</div>
    </div>

    <div class="holder">Tobias Wrenfeld <span class="holder__credentials">- DOE, CPT, LMT</span></div>

    <div class="contact">
      <div class="contact__address">
        4100 East Marrow Drive<br>
        Austin, TX 78119
      </div>
      <div class="contact__group">
        <div class="contact__row">
          <svg class="contact__icon" viewBox="0 0 24 24" aria-hidden="true"><path d="M6.6 10.8a15.1 15.1 0 0 0 6.6 6.6l2.2-2.2a1 1 0 0 1 1-.25 11.4 11.4 0 0 0 3.6.57 1 1 0 0 1 1 1V20a1 1 0 0 1-1 1A17 17 0 0 1 3 4a1 1 0 0 1 1-1h3.5a1 1 0 0 1 1 1c0 1.25.2 2.45.57 3.570a1 1 0 0 1-.25 1z"/></svg>
          512 555 0148
        </div>
        <div class="contact__row">
          <svg class="contact__icon" viewBox="0 0 24 24" aria-hidden="true"><path d="M7 1h10a2 2 0 0 1 2 2v18a2 2 0 0 1-2 2H7a2 2 0 0 1-2-2V3a2 2 0 0 1 2-2zm0 3v14h10V4zm5 15.5a1 1 0 1 0 0 2 1 1 0 0 0 0-2z"/></svg>
          818 555 0192
        </div>
      </div>
      <div class="contact__group">
        <div class="contact__row">
          <svg class="contact__icon" viewBox="0 0 24 24" aria-hidden="true"><path d="M2 5h20v14H2zm2 2v.4l8 5.2 8-5.2V7zm16 2.8-8 5.2-8-5.2V17h16z"/></svg>
          info@ValmiraHealth.example
        </div>
        <div class="contact__row">
          <svg class="contact__icon" viewBox="0 0 24 24" aria-hidden="true"><path d="M2 5h20v14H2zm2 2v.4l8 5.2 8-5.2V7zm16 2.8-8 5.2-8-5.2V17h16z"/></svg>
          t.wrenfeld@ValmiraHealth.example
        </div>
      </div>
    </div>
  </section>

  <section class="card card--brand" aria-label="Business card, brand side">
    <div class="brand">
      <div class="brand__name"><span class="brand__dot"></span>Valmira</div>
      <div class="brand__tagline">Integrative Holistic Medicine</div>
    </div>
    <div class="motto-band">helping the body help itself</div>
  </section>

</body>
</html>
```